New Business Card Design for Manufacturing

We are an engineering/manufacturing company that offers Advanced machining/assembly/engineering services, as well as innovative products for the heavy duty engine cooling markets.

We are looking to get a new business card designed that is clean and modern looking, but still fits the wide range of technical/skilled work we do.

- We hope to use this design as the base for other design work in new Presentations, web, and print work.

Industry/Entity Type

Engineering

Contact Information for Business Card

Our preferred color of blue is (RGB) 22/71/159 but can vary slightly from that color. Our content will be our Logo and full company name (Vantrell Forge Works, Inc.), company address, name, job title, phone number with extension, cell number, fax number, website, and email address on the cards.
We'd like the full company name next to the logo, but we are open to other interpretations of that layout.
Preferably, we would like the back side to be clean with just our logo, and the front to contain all of the contact information.

Colors
2f74b4
0355a3
85abd2

Requirements
Must have
• - Logo, company name, needed content - We are open to interpretation beyond that.
• - Standard size business card.
• - Horizontal orientation.
• - Enough space for lengthy names / job titles (for example, a job title could read "Directory of Human Resources" or "V.P. of Governmental Affairs"). We need this to look clean, whether the title be short (CEO) or long (as described above).

```html
<!DOCTYPE html>
<html lang="en">
<head>
<meta charset="utf-8">
<title>Vantrell Forge Works – Business Card</title>
<link href="https://fonts.googleapis.com/css2?family=Roboto:wght@400;500;700&family=Roboto+Condensed:wght@500&display=swap" rel="stylesheet">
<style>
  :root {
    --brand-blue: #1351a0;
    --ink: #333333;
    --muted: #555555;
    --tagline-grey: #7d7f82;
    --card-white: #f7f7f7;
    --divider: #b5b5b5;
    --backdrop: #e6e4e1;
  }
  * { margin: 0; padding: 0; box-sizing: border-box; }
  html, body { width: 1200px; height: 960px; overflow: hidden; }
  body {
    position: relative;
    background: var(--backdrop);
    font-family: "Roboto", Arial, sans-serif;
  }
  .card {
    position: absolute;
    width: 600px;
    height: 341px;
    border-radius: 20px;
    box-shadow: 2px 4px 8px rgba(0,0,0,0.25);
  }
  .card-front { left: 302px; top: 130px; background: var(--card-white); }
  .card-back { left: 298px; top: 489px; background: var(--brand-blue); }

  /* front: brand lockup */
  .brand-lockup {
    position: absolute;
    left: 90px;
    top: 66px;
    display: flex;
    align-items: center;
    gap: 14px;
  }
  .brand-square {
    width: 58px; height: 58px;
    background: var(--brand-blue);
  }
  .brand-name {
    font-weight: 700;
    font-size: 21px;
    line-height: 21px;
    color: var(--brand-blue);
    text-transform: uppercase;
    letter-spacing: 0.3px;
  }
  .brand-tagline-front {
    position: absolute;
    left: 90px;
    top: 142px;
    font-weight: 700;
    font-size: 15px;
    color: var(--tagline-grey);
    letter-spacing: 0.2px;
  }

  /* front: person */
  .person {
    position: absolute;
    right: 356px;
    top: 200px;
    text-align: right;
    white-space: nowrap;
  }
  .person-name {
    font-family: "Roboto Condensed", "Arial Narrow", sans-serif;
    font-weight: 500;
    font-size: 23px;
    line-height: 28px;
    color: var(--brand-blue);
    text-transform: uppercase;
  }
  .person-title { font-size: 14px; line-height: 19px; color: var(--ink); }
  .person-address { font-size: 14px; line-height: 19px; color: var(--muted); }

  .divider {
    position: absolute;
    left: 261px;
    top: 203px;
    width: 1px;
    height: 78px;
    background: var(--divider);
  }

  .contact-list {
    position: absolute;
    left: 279px;
    top: 202px;
    list-style: none;
  }
  .contact-item {
    display: flex;
    align-items: center;
    gap: 7px;
    font-size: 14px;
    line-height: 19.5px;
    color: var(--muted);
  }
  .contact-icon { width: 13px; height: 13px; fill: var(--brand-blue); flex: none; }

  /* back */
  .back-brand {
    position: absolute;
    left: 0; right: 0;
    top: 110px;
    text-align: center;
    font-weight: 700;
    font-size: 54px;
    line-height: 60px;
    color: #ffffff;
    text-transform: uppercase;
    letter-spacing: 1px;
  }
  .back-tagline {
    position: absolute;
    left: 0; right: 0;
    top: 202px;
    text-align: center;
    font-weight: 700;
    font-size: 18px;
    color: #ffffff;
  }
  .back-website {
    position: absolute;
    left: 0; right: 0;
    top: 283px;
    text-align: center;
    font-size: 14px;
    letter-spacing: 2.4px;
    color: #ffffff;
  }
</style>
</head>
<body>
  <section class="card card-front" aria-label="Business card front">
    <div class="brand-lockup">
      <div class="brand-square"></div>
      <div class="brand-name">Vantrell<br>Forge Works<br>Inc.</div>
    </div>
    <div class="brand-tagline-front">SHAPING WHAT'S NEXT</div>

    <div class="person">
      <div class="person-name">Dana Whitfield</div>
      <div class="person-title">V.P. of Governmental Affairs</div>
      <div class="person-address">1420 Larkspur Road</div>
      <div class="person-address">Fairbanks, Alaska 99701</div>
    </div>

    <div class="divider"></div>

    <ul class="contact-list">
      <li class="contact-item">
        <svg class="contact-icon" viewBox="0 0 24 24"><path d="M6.6 10.8a15.1 15.1 0 0 0 6.6 6.6l2.2-2.2a1 1 0 0 1 1-.25 11.4 11.4 0 0 0 3.6.57 1 1 0 0 1 1 1V20a1 1 0 0 1-1 1A17 17 0 0 1 3 4a1 1 0 0 1 1-1h3.5a1 1 0 0 1 1 1c0 1.25.2 2.45.57 3.57a1 1 0 0 1-.25 1z"/></svg>
        555 214 7730
      </li>
      <li class="contact-item">
        <svg class="contact-icon" viewBox="0 0 24 24"><path d="M7 1h10a2 2 0 0 1 2 2v18a2 2 0 0 1-2 2H7a2 2 0 0 1-2-2V3a2 2 0 0 1 2-2zm0 3v14h10V4zm5 15.5a1.2 1.2 0 1 0 0 2.4 1.2 1.2 0 0 0 0-2.4z"/></svg>
        555 382 6491
      </li>
      <li class="contact-item">
        <svg class="contact-icon" viewBox="0 0 24 24"><path d="M2 5h20v14H2zm2 2v.5l8 5 8-5V7zm0 2.8V17h16V9.8l-8 5z"/></svg>
        dana@vantrellforgeworks.com
      </li>
      <li class="contact-item">
        <svg class="contact-icon" viewBox="0 0 24 24"><path d="M12 2a10 10 0 1 0 0 20 10 10 0 0 0 0-20zm-1 17.9A8 8 0 0 1 4.2 10.6L9 15.4v1a2 2 0 0 0 2 2zm6.9-2.5a2 2 0 0 0-1.9-1.4h-1v-3a1 1 0 0 0-1-1H8v-2h2a1 1 0 0 0 1-1V7h2a2 2 0 0 0 2-2v-.4a8 8 0 0 1 2.9 12.8z"/></svg>
        www.vantrellforgeworks.com
      </li>
    </ul>
  </section>

  <section class="card card-back" aria-label="Business card back">
    <div class="back-brand">Vantrell</div>
    <div class="back-tagline">SHAPING WHAT'S NEXT</div>
    <div class="back-website">www.vantrellforgeworks.com</div>
  </section>
</body>
</html>
```